Architectural, Engineering and Design Build

Tovandex4.com
Veteran Disabled Certified company is doing business in Architecture, Engineer and Design build - look simialr websites and come up with design follow following website
https://hollis-darnet.example/
https://www.venlorcogroup.example/
https://www.pembrisgc.example/contract-vehicles/service-disabled-veteran-owned-small-business-sdvosb/
https://www.corbelnetlink.example/about/sdvosb/

Target Market(s)

US - Defense and Federal Government

Industry/Entity Type

Colors
0054AA
0677BA
7BADD7
CADEEF
E8F1F8

Requirements
Must have
• Army, American patriotism , Buildings, construction, architecture, engineering
Nice to have
• I need to attract federal government agencies and Defense

```html
<!DOCTYPE html>
<html lang="en">
<head>
<meta charset="utf-8">
<title>Tovandex4 — Architecture, Engineering &amp; Design Build</title>
<link href="https://fonts.googleapis.com/css2?family=Chakra+Petch:wght@600;700&family=Roboto:wght@400;500;700&display=swap" rel="stylesheet">
<style>
:root{
  --navy:#17206a;
  --navy-deep:#0f1650;
  --red:#e0121f;
  --red-deep:#b80d18;
  --white:#ffffff;
  --ink:#1b1b1b;
  --muted:#6a6a6a;
  --paper:#f6f4f1;
  --dark:#141414;
}
*{margin:0;padding:0;box-sizing:border-box}
html,body{width:1200px;height:4601px;overflow:hidden}
body{position:relative;background:var(--white);font-family:"Roboto",Arial,sans-serif;color:var(--ink)}
.abs{position:absolute}
.heading{font-family:"Chakra Petch","Arial Black",sans-serif;font-weight:700;text-transform:uppercase;letter-spacing:1px}
.btn{position:absolute;display:flex;align-items:center;justify-content:center;border-radius:30px;font-weight:700;color:var(--white);font-size:16px;white-space:nowrap}
.btn-red{background:var(--red)}
.btn-navy{background:var(--navy)}

/* header */
.top-line{left:0;top:0;width:1200px;height:5px;background:var(--red)}
.logo-holder{left:110px;top:-10px;width:230px;height:245px;border-radius:0 0 115px 115px;background:var(--white);display:flex;align-items:center;justify-content:center;z-index:5}
.logo-word{font-family:"Chakra Petch",sans-serif;font-weight:700;font-size:36px;color:var(--navy);letter-spacing:1px}
.contact-item{top:28px;display:flex;align-items:center;gap:14px}
.contact-icon{width:44px;height:44px;border-radius:50%;background:var(--navy);display:flex;align-items:center;justify-content:center}
.contact-label{font-size:11px;color:var(--navy)}
.contact-value{font-size:17px;font-weight:700;color:var(--ink);white-space:nowrap}
.nav-bar{left:371px;top:107px;width:829px;height:63px;background:var(--red);border-radius:14px 0 0 0}
.nav-link{position:absolute;top:22px;font-size:13px;font-weight:500;color:var(--white)}
.nav-join{left:563px;top:14px;width:152px;height:36px;font-size:13px}

/* hero */
.hero-photo{left:0;top:170px;width:1200px;height:640px;background:linear-gradient(180deg,#4d5866 0%,#6a6a6e 35%,#b06a48 62%,#e59a50 72%,#3a2c2a 100%)}
.hero-title{left:0;top:375px;width:1200px;text-align:center;font-size:58px;color:var(--white);text-shadow:0 2px 6px rgba(0,0,0,.35)}
.hero-title span{color:var(--red)}
.hero-text{left:190px;top:466px;width:820px;text-align:center;font-size:17px;line-height:38px;color:var(--white)}
.scroll-dot{left:578px;top:776px;width:44px;height:44px;border-radius:50%;background:var(--white);box-shadow:0 3px 10px rgba(0,0,0,.2);display:flex;align-items:center;justify-content:center}

/* about */
.about-bg{left:0;top:820px;width:1200px;height:720px;background:linear-gradient(120deg,#fff 30%,#fbe9ea 55%,#fff 80%)}
.about-splash{left:0;top:1200px;width:460px;height:245px;background:linear-gradient(100deg,#1f2a78 0%,#e8eaf4 45%,#e0121f 80%,#fff 100%);opacity:.55}
.about-ring{left:125px;top:929px;width:446px;height:446px;border-radius:50%;border:3px solid var(--red);background:var(--white);padding:14px}
.about-ring-inner{width:100%;height:100%;border-radius:50%;background:var(--navy);padding:24px}
.about-photo{width:100%;height:100%;border-radius:50%;background:linear-gradient(180deg,#e6ddd0 0%,#d9c9a8 50%,#8a8a5a 100%)}
.section-title{font-size:40px;color:var(--ink)}
.about-title{left:639px;top:940px}
.about-text{left:639px;width:440px;font-size:14px;line-height:31.5px;color:var(--muted)}

/* offer */
.offer-bg{left:0;top:1500px;width:1200px;height:779px;background:linear-gradient(160deg,#eef0f8 0%,#fbfbfd 40%,#fde9ea 75%,#eef0f8 100%)}
.center-title{left:0;width:1200px;text-align:center}
.center-text{left:150px;width:900px;text-align:center;font-size:13.5px;line-height:29px;color:var(--muted)}
.offer-card{top:1754px;width:315px;height:432px;border-radius:32px;overflow:hidden;background:var(--red);box-shadow:0 6px 16px rgba(0,0,0,.12)}
.offer-card.navy{background:var(--navy)}
.offer-photo{width:100%;height:219px}
.offer-icon{position:absolute;left:28px;top:200px;width:64px;height:64px;border-radius:50%;background:var(--navy);border:4px solid var(--white);display:flex;align-items:center;justify-content:center}
.offer-card.navy .offer-icon{background:var(--red)}
.offer-name{position:absolute;left:34px;top:280px;font-size:16px;color:var(--white)}
.offer-text{position:absolute;left:34px;top:314px;width:260px;font-size:11.5px;line-height:24px;color:var(--white)}
.offer-more{position:absolute;left:34px;top:394px;font-size:11.5px;color:var(--navy);text-decoration:underline;font-weight:500}
.offer-card.navy .offer-more{color:var(--red)}

/* testimonials */
.testi-photo{left:0;top:2279px;width:1200px;height:680px;background:linear-gradient(180deg,#6d6a72 0%,#b3a79a 40%,#e8c89a 58%,#6a5b52 100%)}
.testi-title{left:112px;top:2372px;color:var(--white);font-size:40px}
.testi-quote{left:112px;top:2448px;font-family:"Chakra Petch",sans-serif;font-weight:700;font-size:72px;line-height:60px;color:var(--white)}
.testi-text{left:112px;width:420px;font-size:14px;line-height:31.6px;color:var(--white)}
.testi-name{left:112px;top:2756px;font-size:13px;color:var(--red)}
.round-arrow{width:34px;height:34px;border-radius:50%;background:var(--white);display:flex;align-items:center;justify-content:center;box-shadow:0 2px 6px rgba(0,0,0,.2)}

/* blogs */
.blog-bg{left:0;top:2960px;width:1200px;height:1080px;background:var(--paper)}
.blog-card{top:3186px;width:315px}
.blog-photo{width:315px;height:257px}
.blog-date{position:absolute;left:24px;top:238px;width:89px;height:35px;border-radius:8px;background:var(--red);color:var(--white);font-size:12px;font-weight:700;display:flex;align-items:center;justify-content:center}
.blog-head{position:absolute;left:26px;top:290px;width:280px;font-size:13.5px;font-weight:700;line-height:28px;color:var(--ink)}
.blog-text{position:absolute;left:26px;top:356px;width:280px;font-size:10px;line-height:22.5px;color:var(--muted)}

/* contact + footer */
.footer-bg{left:0;top:4036px;width:1200px;height:565px;background:linear-gradient(180deg,#2a0d10 0%,#171212 40%,#0e0e0e 100%)}
.contact-box{left:112px;top:3725px;width:976px;height:502px;border-radius:54px;background:linear-gradient(120deg,#ff2a36 0%,var(--red) 45%,#c90e1a 100%)}
.contact-photo{left:143px;top:3768px;width:411px;height:418px;border-radius:36px;background:linear-gradient(160deg,#d8e4f2 0%,#8aa4c8 45%,#2a3b5e 100%)}
.contact-title{left:605px;top:3780px;font-size:40px;color:var(--white)}
.contact-sub{left:605px;top:3841px;font-size:14px;color:var(--white)}
.field{position:absolute;background:var(--navy);border-radius:6px;color:var(--white);font-size:11.5px;padding:13px 16px}
.send{left:605px;top:4146px;font-size:12px;font-weight:700;color:var(--white);text-decoration:underline;letter-spacing:.5px}
.foot-logo{left:500px;top:4290px;width:200px;height:130px;display:flex;align-items:center;justify-content:center}
.foot-logo .logo-word{color:var(--white)}
.foot-link{position:absolute;top:4455px;font-size:13px;font-weight:500;color:var(--white)}
.social{position:absolute;top:4500px;width:36px;height:36px;border-radius:50%;background:var(--red)}
.copyright{left:0;top:4557px;width:1200px;text-align:center;font-size:11px;color:var(--white)}
</style>
</head>
<body>

<!-- HEADER -->
<div class="abs top-line"></div>
<div class="abs logo-holder"><span class="logo-word">TOVANDEX4</span></div>

<div class="abs contact-item" style="left:646px">
  <div class="contact-icon"><svg width="18" height="18" viewBox="0 0 24 24"><path d="M6.6 10.8c1.4 2.8 3.8 5.1 6.6 6.6l2.2-2.2c.3-.3.7-.4 1-.2 1.1.4 2.3.6 3.6.6.6 0 1 .4 1 1V20c0 .6-.4 1-1 1C10.6 21 3 13.4 3 4c0-.6.4-1 1-1h3.5c.6 0 1 .4 1 1 0 1.3.2 2.5.6 3.6.1.3 0 .7-.2 1z" fill="#fff"/></svg></div>
  <div><div class="contact-label">Call Us:</div><div class="contact-value">+1 555 014 2290</div></div>
</div>
<div class="abs contact-item" style="left:884px">
  <div class="contact-icon"><svg width="18" height="18" viewBox="0 0 24 24"><path d="M3 5h18v14H3z" fill="#fff"/><path d="M3 5l9 7 9-7" fill="none" stroke="#17206a" stroke-width="2"/></svg></div>
  <div><div class="contact-label">Email Us:</div><div class="contact-value">info@tovandex4.com</div></div>
</div>

<nav class="abs nav-bar">
  <span class="nav-link" style="left:45px">Home</span>
  <span class="nav-link" style="left:138px">About Us</span>
  <span class="nav-link" style="left:250px">Services</span>
  <span class="nav-link" style="left:359px">Reviews</span>
  <span class="nav-link" style="left:466px">Contact Us</span>
  <span class="btn btn-navy nav-join">Join With Us</span>
</nav>

<!-- HERO -->
<div class="abs hero-photo" role="img" aria-label="Statue of Liberty silhouetted against a sunset sky with faint stars"></div>
<svg class="abs" style="left:0;top:600px" width="1200" height="260" viewBox="0 600 1200 260">
  <path d="M0 688 Q600 884 1200 688 L1200 860 L0 860 Z" fill="#fff"/>
  <path d="M0 676 Q600 872 1200 676" fill="none" stroke="#17206a" stroke-width="4"/>
  <path d="M0 700 Q600 908 1200 700" fill="none" stroke="#e0121f" stroke-width="4"/>
</svg>
<h1 class="abs heading hero-title">Welcome to <span>Tovandex4</span></h1>
<p class="abs hero-text">Lorem ipsum dolor sit amet, consectetur adipiscing elit, sed do eiusmod tempor incididunt ut labore et dolore magna aliqua. Quis ipsum suspendisse ultrices gravida.</p>
<span class="btn btn-red" style="left:418px;top:577px;width:146px;height:45px">Get Started</span>
<span class="btn btn-navy" style="left:591px;top:577px;width:189px;height:45px">+1 555 014 2290</span>
<div class="abs scroll-dot"><svg width="14" height="24" viewBox="0 0 14 24"><path d="M3 8l4-4 4 4M3 16l4 4 4-4" fill="none" stroke="#17206a" stroke-width="2"/><circle cx="7" cy="12" r="2" fill="#17206a"/></svg></div>

<!-- ABOUT -->
<div class="abs about-bg" role="img" aria-label="Faint waving flag in soft red and white behind the about section"></div>
<div class="abs about-splash" role="img" aria-label="Painted brush splash in navy, white and red"></div>
<div class="abs about-ring"><div class="about-ring-inner"><div class="about-photo" role="img" aria-label="Soldier carrying a child holding a flag in a golden field"></div></div></div>
<h2 class="abs heading section-title about-title">About Us</h2>
<p class="abs about-text" style="top:1005px">Lorem ipsum dolor sit amet, consectetur adipiscing elit, sed do eiusmod tempor incididunt ut labore et dolore magna aliqua. Quis ipsum suspendisse ultrices gravida. Risus commodo viverra maecenas accumsan lacus vel facilisis. Lorem ipsum dolor sit amet, consectetur adipiscing elit, sed do eiusmod tempor incididunt ut labore et dolore magna aliqua. Quis ipsum suspendisse ultrices gravida.</p>
<p class="abs about-text" style="top:1225px">Consectetur adipiscing elit, sed do eiusmod tempor incididunt ut labore et dolore magna aliqua.</p>
<span class="btn btn-red" style="left:639px;top:1313px;width:118px;height:37px;font-size:13px">Read More</span>

<!-- WHAT WE OFFER -->
<div class="abs offer-bg" role="img" aria-label="Soft faded flag pattern in navy, white and red"></div>
<svg class="abs" style="left:0;top:1480px" width="1200" height="150" viewBox="0 1480 1200 150">
  <path d="M0 1480 L1200 1480 L1200 1616 Q600 1402 0 1616 Z" fill="#fff"/>
  <path d="M0 1616 Q600 1402 1200 1616" fill="none" stroke="#17206a" stroke-width="4"/>
</svg>
<h2 class="abs heading section-title center-title" style="top:1592px">What We Offer</h2>
<p class="abs center-text" style="top:1661px">Lorem ipsum dolor sit amet, consectetur adipiscing elit, sed do eiusmod tempor incididunt ut labore et dolore magna aliqua. Quis ipsum suspendisse ultrices gravida. Risus commodo viverra maecenas accumsan lacus vel facilisis.</p>

<div class="abs offer-card" style="left:112px">
  <div class="offer-photo" role="img" aria-label="Hands sketching architectural floor plans" style="background:linear-gradient(150deg,#f4f2ee,#cfc9c0 60%,#a89c8e)"></div>
  <div class="offer-icon"><svg width="28" height="28" viewBox="0 0 24 24"><rect x="4" y="4" width="16" height="16" fill="none" stroke="#fff" stroke-width="1.8"/><path d="M8 16l8-8" stroke="#fff" stroke-width="1.8"/></svg></div>
  <h3 class="heading offer-name">Architecture</h3>
  <p class="offer-text">Lorem ipsum dolor sit amet, consectetur adipiscing elit, sed do eiusmod tempor incididunt ut labore et dolore magna aliqua.</p>
  <span class="offer-more">View More</span>
</div>
<div class="abs offer-card navy" style="left:443px">
  <div class="offer-photo" role="img" aria-label="Engineers in safety vests on a construction site with cranes" style="background:linear-gradient(180deg,#8fb4d8,#c4d6e6 55%,#8a8f94)"></div>
  <div class="offer-icon"><svg width="28" height="28" viewBox="0 0 24 24"><circle cx="12" cy="10" r="5" fill="none" stroke="#fff" stroke-width="1.8"/><path d="M5 20c1-4 13-4 14 0" fill="none" stroke="#fff" stroke-width="1.8"/></svg></div>
  <h3 class="heading offer-name">Engineering</h3>
  <p class="offer-text">Lorem ipsum dolor sit amet, consectetur adipiscing elit, sed do eiusmod tempor incididunt ut labore et dolore magna aliqua.</p>
  <span class="offer-more">View More</span>
</div>
<div class="abs offer-card" style="left:771px">
  <div class="offer-photo" role="img" aria-label="Wireframe sketch of a modern building beside the finished house" style="background:linear-gradient(120deg,#f2f2f0,#d8d6d0 55%,#9a958c)"></div>
  <div class="offer-icon"><svg width="28" height="28" viewBox="0 0 24 24"><path d="M12 3l7 7-7 11-7-11z" fill="none" stroke="#fff" stroke-width="1.8"/><circle cx="12" cy="11" r="2" fill="#fff"/></svg></div>
  <h3 class="heading offer-name">Design Build</h3>
  <p class="offer-text">Lorem ipsum dolor sit amet, consectetur adipiscing elit, sed do eiusmod tempor incididunt ut labore et dolore magna aliqua.</p>
  <span class="offer-more">View More</span>
</div>

<!-- TESTIMONIALS -->
<div class="abs testi-photo" role="img" aria-label="Man holding a flag overhead against a cloudy sunset sky"></div>
<svg class="abs" style="left:0;top:2279px" width="1200" height="700" viewBox="0 2279 1200 700">
  <polygon points="0,2279 518,2279 652,2979 0,2979" fill="#17206a"/>
  <path d="M0 2777 Q600 3009 1200 2777 L1200 2979 L0 2979 Z" fill="#f6f4f1"/>
  <path d="M0 2766 Q600 2998 1200 2766" fill="none" stroke="#fff" stroke-width="5"/>
  <path d="M0 2777 Q600 3009 1200 2777" fill="none" stroke="#17206a" stroke-width="4"/>
</svg>
<h2 class="abs heading testi-title">Testimonials</h2>
<div class="abs testi-quote">&#8221;</div>
<p class="abs testi-text" style="top:2520px">I must explain to you how all this mistaken idea of denouncing pleasure and praising pain was born and I will give you a complete account of the system, and expound the actual teachings of the great explorer of the truth</p>
<p class="abs testi-text" style="top:2677px">No one rejects, dislikes, or avoids pleasure itself, because it is pleasure.</p>
<div class="abs testi-name">DANIEL CORWIN</div>
<div class="abs round-arrow" style="left:485px;top:2805px"><svg width="12" height="12" viewBox="0 0 12 12"><path d="M6 2L2 6l4 4M10 2L6 6l4 4" fill="none" stroke="#17206a" stroke-width="1.6"/></svg></div>
<div class="abs round-arrow" style="left:531px;top:2805px"><svg width="12" height="12" viewBox="0 0 12 12"><path d="M2 2l4 4-4 4M6 2l4 4-4 4" fill="none" stroke="#17206a" stroke-width="1.6"/></svg></div>

<!-- BLOGS -->
<div class="abs blog-bg"></div>
<h2 class="abs heading section-title center-title" style="top:3020px">Latest Blogs &amp; News</h2>
<p class="abs center-text" style="top:3088px">Lorem ipsum dolor sit amet, consectetur adipiscing elit, sed do eiusmod tempor incididunt ut labore et dolore magna aliqua. Quis ipsum suspendisse ultrices gravida. Risus commodo viverra maecenas accumsan lacus vel facilisis.</p>

<div class="abs round-arrow" style="left:37px;top:3376px"><svg width="12" height="12" viewBox="0 0 12 12"><path d="M6 2L2 6l4 4M10 2L6 6l4 4" fill="none" stroke="#17206a" stroke-width="1.6"/></svg></div>
<div class="abs round-arrow" style="left:1127px;top:3376px"><svg width="12" height="12" viewBox="0 0 12 12"><path d="M2 2l4 4-4 4M6 2l4 4-4 4" fill="none" stroke="#17206a" stroke-width="1.6"/></svg></div>

<article class="abs blog-card" style="left:112px">
  <div class="blog-photo" role="img" aria-label="Floor plans on a desk with sticky notes and glasses" style="background:linear-gradient(150deg,#f3f1ec,#d4d0c8 60%,#b9a896)"></div>
  <span class="blog-date">13/06/2024</span>
  <h3 class="blog-head">Lorem ipsum dolor sit amet, consectetur adipiscing elit, sed do eiusmod</h3>
  <p class="blog-text">Lorem ipsum dolor sit amet, consectetur adipiscing elit, sed do eiusmod tempor incididunt ut labore et dolore magna aliqua. Quis ipsum suspendisse ultrices gravida.</p>
</article>
<article class="abs blog-card" style="left:443px">
  <div class="blog-photo" role="img" aria-label="Glass office tower seen from below at dusk" style="background:linear-gradient(180deg,#2e5e9a,#3c4f70 55%,#c8924a)"></div>
  <span class="blog-date">13/06/2024</span>
  <h3 class="blog-head">Lorem ipsum dolor sit amet, consectetur adipiscing elit, sed do eiusmod</h3>
  <p class="blog-text">Lorem ipsum dolor sit amet, consectetur adipiscing elit, sed do eiusmod tempor incididunt ut labore et dolore magna aliqua. Quis ipsum suspendisse ultrices gravida.</p>
</article>
<article class="abs blog-card" style="left:771px">
  <div class="blog-photo" role="img" aria-label="Soldier saluting in front of a flag at sunset" style="background:linear-gradient(120deg,#3a3632,#6e5a48 55%,#d88a52)"></div>
  <span class="blog-date">13/06/2024</span>
  <h3 class="blog-head">Lorem ipsum dolor sit amet, consectetur adipiscing elit, sed do eiusmod</h3>
  <p class="blog-text">Lorem ipsum dolor sit amet, consectetur adipiscing elit, sed do eiusmod tempor incididunt ut labore et dolore magna aliqua. Quis ipsum suspendisse ultrices gravida.</p>
</article>

<!-- CONTACT -->
<div class="abs footer-bg" role="img" aria-label="Dark waving flag in deep red and black"></div>
<div class="abs contact-box"></div>
<div class="abs contact-photo" role="img" aria-label="Curving glass facade of a modern building"></div>
<h2 class="abs heading contact-title">Get In Touch</h2>
<p class="abs contact-sub">We denounce with righteous indignation and dislike men</p>
<div class="field" style="left:605px;top:3886px;width:213px;height:39px">First Name</div>
<div class="field" style="left:839px;top:3886px;width:213px;height:39px">Last Name</div>
<div class="field" style="left:605px;top:3952px;width:213px;height:39px">Email Address</div>
<div class="field" style="left:839px;top:3952px;width:213px;height:39px">Contact Number</div>
<div class="field" style="left:605px;top:4018px;width:447px;height:107px">Message</div>
<div class="abs send">SEND MESSAGE</div>

<!-- FOOTER -->
<div class="abs foot-logo"><span class="logo-word">TOVANDEX4</span></div>
<span class="foot-link" style="left:356px">Home</span>
<span class="foot-link" style="left:449px">About Us</span>
<span class="foot-link" style="left:562px">Services</span>
<span class="foot-link" style="left:670px">Reviews</span>
<span class="foot-link" style="left:777px">Contact Us</span>
<span class="social" style="left:509px"></span>
<span class="social" style="left:557px"></span>
<span class="social" style="left:605px"></span>
<span class="social" style="left:655px"></span>
<div class="abs copyright">(C) Copyright 2024 | All Rights Reserved</div>

</body>
</html>
```